Landing Page Design for Adult Dating Age Verification (18+)

The objective of this task is to design a visually appealing pre-landing page for the adult dating site "Quillmera (site: https://quillmera.com/)" with an age verification mechanism. The pre-landing page will feature two buttons that redirect visitors to the main offer. The design should also include a footer block that includes links to the terms of use, privacy policy, and contact us pages.

Design Requirements:
Develop an age verification section prominently displayed on the pre-landing page.
Design the section to include two buttons labeled "Yes" and "No" for visitors to confirm their age.
Ensure the section is visually appealing and clearly communicates the purpose of age verification.

Visual Appeal:
Create a visually appealing design that aligns with the branding and theme of the "Quillmera" adult dating site.
Use suitable color schemes, typography, and graphics to enhance the overall visual appeal of the pre-landing page.

Layout and Navigation:
Design an engaging and intuitive layout that encourages visitors to interact with the page and proceed to the main offer.
Ensure clear and visible navigation elements that direct visitors to the main offer or provide additional information.

Responsive Design:
Develop a responsive design that provides a seamless user experience across various devices, including desktop and mobile.
Ensure the design elements and layout adapt well to different screen sizes and resolutions.

File Formats and Assets:
Deliver the final design in PSD, AI, or Sketch format, ensuring that the files are well-organized and layered.
Include any necessary images or assets used in the design, ensuring they are of high quality and optimized for web use.

```html
<!DOCTYPE html>
<html lang="en">
<head>
<meta charset="utf-8">
<title>Quillmera — Age Verification</title>
<link rel="stylesheet" href="https://fonts.googleapis.com/css2?family=DM+Serif+Display&family=Crimson+Text:wght@400;600&display=swap">
<style>
  :root {
    --lilac: #d4b5d7;
    --lilac-soft: #dcc3df;
    --ink: #111111;
    --navy: #23223a;
    --white: #ffffff;
    --header-veil: rgba(235, 232, 228, 0.42);
  }
  * { margin: 0; padding: 0; box-sizing: border-box; }
  html, body {
    width: 1200px;
    height: 669px;
    overflow: hidden;
  }
  body {
    position: relative;
    font-family: "Crimson Text", Georgia, serif;
    color: var(--ink);
    background: #6b5a4a;
  }
  .hero-photo {
    position: absolute;
    inset: 0 0 55px 0;
    background:
      radial-gradient(ellipse 30% 45% at 55% 40%, rgba(196, 140, 108, 0.9), transparent 70%),
      radial-gradient(ellipse 25% 35% at 12% 45%, rgba(220, 226, 238, 0.95), transparent 75%),
      radial-gradient(ellipse 30% 40% at 80% 70%, rgba(236, 232, 226, 0.85), transparent 75%),
      linear-gradient(100deg, #a7a9b3 0%, #c7a088 35%, #a0684b 55%, #8b7a5e 80%, #5e5a3e 100%);
  }
  .site-header {
    position: absolute;
    top: 0; left: 0; right: 0;
    height: 99px;
    background: var(--header-veil);
    display: flex;
    align-items: center;
    padding: 0 111px;
  }
  .brand {
    display: flex;
    align-items: center;
    gap: 12px;
    font-family: "DM Serif Display", Georgia, serif;
    font-size: 43px;
    color: var(--navy);
    text-decoration: none;
  }
  .brand-dot {
    width: 30px; height: 30px;
    border-radius: 50%;
    background: var(--lilac);
  }
  .main-nav {
    margin-left: auto;
    display: flex;
    gap: 34px;
    font-size: 16px;
  }
  .main-nav a { color: var(--white); text-decoration: none; }
  .main-nav .join-link { color: var(--lilac-soft); }
  .lang-select { display: flex; align-items: center; gap: 4px; }
  .age-gate {
    position: absolute;
    left: 284px; top: 209px;
    width: 626px; height: 302px;
    background: var(--white);
    border-radius: 14px;
    text-align: center;
  }
  .age-gate-frame {
    position: absolute;
    left: 290px; top: 198px;
    width: 630px; height: 305px;
    border: 3px solid var(--lilac);
    border-radius: 18px;
    pointer-events: none;
  }
  .age-gate h1 {
    font-family: "DM Serif Display", Georgia, serif;
    font-weight: 400;
    font-size: 38px;
    letter-spacing: 0.5px;
    margin-top: 76px;
  }
  .age-gate p {
    font-size: 15px;
    margin-top: 4px;
  }
  .age-actions {
    display: flex;
    justify-content: center;
    gap: 23px;
    margin-top: 25px;
  }
  .age-btn {
    width: 54px; height: 43px;
    border: none;
    border-radius: 7px;
    background: var(--lilac);
    color: var(--white);
    font-family: "Crimson Text", Georgia, serif;
    font-size: 21px;
    cursor: pointer;
  }
  .site-footer {
    position: absolute;
    left: 0; right: 0; bottom: 0;
    height: 55px;
    background: var(--lilac);
    display: flex;
    align-items: center;
    padding: 0 111px;
    font-size: 15px;
  }
  .site-footer a { color: var(--ink); text-decoration: none; }
  .site-footer .sep { margin: 0 11px; }
</style>
</head>
<body>
  <div class="hero-photo" role="img" aria-label="Photograph of a smiling couple embracing on a bed with white sheets"></div>

  <header class="site-header">
    <a class="brand" href="https://quillmera.com/"><span class="brand-dot"></span>Quillmera</a>
    <nav class="main-nav">
      <a href="#">Sign In</a>
      <a class="join-link" href="#">Join Now</a>
      <a class="lang-select" href="#">English
        <svg width="14" height="8" viewBox="0 0 14 8"><path d="M0 0h14L7 8z" fill="#dcc3df"/></svg>
      </a>
    </nav>
  </header>

  <section class="age-gate">
    <h1>Are You Over The Age Of 18?</h1>
    <p>You Must Be 18 or Over To View Contents On This Page</p>
    <div class="age-actions">
      <button class="age-btn">Yes</button>
      <button class="age-btn">No</button>
    </div>
  </section>
  <div class="age-gate-frame"></div>

  <footer class="site-footer">
    <a href="#">Terms of Use</a><span class="sep">|</span>
    <a href="#">Privacy Policy</a><span class="sep">|</span>
    <a href="#">Contact Us</a>
  </footer>
</body>
</html>
```